Upscale business cards needed for Board of Directors

We need professional business cards created for members of our family business Board of Directors. We would like these relatively simple and straightforward, but also with a unique element to set them apart. Probably stick with neutral and simple colors - white, grey etc. We need space for the traditional elements, including name, title, address, email/phone number. And we will be creating several from this template so it needs to be template that is easy to switch information in and out of.
Business
See description

```html
<!DOCTYPE html>
<html lang="en">
<head>
<meta charset="UTF-8">
<title>Braxmoor Holdings – Business Card</title>
<link href="https://fonts.googleapis.com/css2?family=Open+Sans:wght@400;600;700;800&display=swap" rel="stylesheet">
<style>
  :root {
    --canvas: #ecebe8;
    --card-dark: #231f20;
    --card-light: #ffffff;
    --gold: #b09a6e;
    --ink: #1e1b1c;
    --text-light: #ffffff;
    --text-muted: #d9d7d5;
    --divider: #4a4647;
  }
  * { margin: 0; padding: 0; box-sizing: border-box; }
  html, body {
    width: 1200px; height: 900px; overflow: hidden;
    background: var(--canvas);
    font-family: "Open Sans", Arial, sans-serif;
  }
  .canvas { position: relative; width: 1200px; height: 900px; }

  .card {
    position: absolute;
    background: var(--card-dark);
    overflow: hidden;
    box-shadow: 0 6px 18px rgba(0,0,0,0.18);
  }
  .band { position: absolute; left: 0; width: 100%; }
  .band--light { background: var(--card-light); }
  .band--gold { background: var(--gold); }

  .wordmark {
    position: absolute;
    color: var(--ink);
    font-weight: 800;
    line-height: 1;
    text-transform: uppercase;
  }
  .wordmark__main { display: block; font-size: 46px; letter-spacing: 0.5px; }
  .wordmark__sub { display: block; font-size: 25px; letter-spacing: 10px; margin-top: 8px; }

  /* Front */
  .card--front { left: 77px; top: 34px; width: 589px; height: 364px; }
  .card--front .band--light { top: 0; height: 155px; }
  .card--front .band--gold { top: 155px; height: 8px; }
  .card--front .wordmark { left: 33px; top: 55px; }
  .card--front .wordmark__sub { margin-left: 43px; }

  .person { position: absolute; left: 31px; top: 191px; color: var(--text-light); }
  .person__name { font-size: 19px; font-weight: 700; line-height: 1.2; }
  .person__title { font-size: 15px; color: var(--text-muted); margin-top: 1px; }

  .contact { position: absolute; left: 0; top: 254px; width: 248px; list-style: none; }
  .contact__item {
    display: flex; align-items: center; gap: 10px;
    height: 32px; padding-left: 33px;
    color: var(--text-light); font-size: 15px;
    border-bottom: 1px solid var(--divider);
  }
  .contact__item:last-child { border-bottom: none; }
  .contact__icon { width: 14px; height: 14px; fill: var(--text-light); flex: none; }

  /* Back */
  .card--back { left: 388px; top: 505px; width: 567px; height: 352px; }
  .card--back .band--gold-top { top: 102px; height: 8px; }
  .card--back .band--light { top: 110px; height: 131px; }
  .card--back .band--gold-bottom { top: 241px; height: 8px; }
  .card--back .wordmark { left: 0; width: 100%; top: 145px; text-align: center; }
  .card--back .wordmark__sub { margin-right: -10px; }
</style>
</head>
<body>
<main class="canvas">

  <section class="card card--front" aria-label="Business card front">
    <div class="band band--light"></div>
    <div class="band band--gold"></div>
    <div class="wordmark">
      <span class="wordmark__main">Braxmoor</span>
      <span class="wordmark__sub">Holdings</span>
    </div>
    <div class="person">
      <p class="person__name">Daniel Carter</p>
      <p class="person__title">Managing Director</p>
    </div>
    <ul class="contact">
      <li class="contact__item">
        <svg class="contact__icon" viewBox="0 0 24 24" aria-hidden="true"><path d="M6.6 10.8c1.4 2.8 3.8 5.1 6.6 6.6l2.2-2.2c.3-.3.7-.4 1-.2 1.1.4 2.3.6 3.6.6.6 0 1 .4 1 1V20c0 .6-.4 1-1 1C10.6 21 3 13.4 3 4c0-.6.4-1 1-1h3.5c.6 0 1 .4 1 1 0 1.3.2 2.5.6 3.6.1.3 0 .7-.2 1z"/></svg>
        <span>044-555 010 203</span>
      </li>
      <li class="contact__item">
        <svg class="contact__icon" viewBox="0 0 24 24" aria-hidden="true"><path d="M3 5h18v14H3z M4 6.5v.6l8 5.4 8-5.4v-.6z" fill-rule="evenodd"/></svg>
        <span>hello@braxmoor.example</span>
      </li>
      <li class="contact__item">
        <svg class="contact__icon" viewBox="0 0 24 24" aria-hidden="true"><path d="M10.6 13.4a1 1 0 0 1 0-1.4l3.5-3.5a1 1 0 1 1 1.4 1.4L12 13.4a1 1 0 0 1-1.4 0zM8 20a4 4 0 0 1-2.8-6.8l2.5-2.5 1.4 1.4-2.5 2.5a2 2 0 1 0 2.8 2.8l2.5-2.5 1.4 1.4-2.5 2.5A4 4 0 0 1 8 20zm8.3-6.7-1.4-1.4 2.5-2.5a2 2 0 1 0-2.8-2.8l-2.5 2.5-1.4-1.4 2.5-2.5a4 4 0 1 1 5.6 5.6z"/></svg>
        <span>www.braxmoor.example</span>
      </li>
    </ul>
  </section>

  <section class="card card--back" aria-label="Business card back">
    <div class="band band--gold band--gold-top"></div>
    <div class="band band--light"></div>
    <div class="band band--gold band--gold-bottom"></div>
    <div class="wordmark">
      <span class="wordmark__main">Braxmoor</span>
      <span class="wordmark__sub">Holdings</span>
    </div>
  </section>

</main>
</body>
</html>
```